Four in One (Flexible infographic for Content Management Industry)

See attachment.
A graphic depicting 4 products, where each can stand on its own and each can be combined with others, but where, if all are taken together, the best result is achieved (the "super product").
Intended use is web. See attached file as an example.
The most basic idea is as the attached diagram shows, where 4 rectangles are arranged in a quadrangle, with a middle rectangle in the center representing the combined 4 products. This concept is fine except it is a bit too obvious as it stands. We are looking for either a variation of this or another concept.
The audience is technical + professional + enterprise - NOT consumers. Hence the design should be conservative in nature.
We are aware of tools like as Canva or Pictogram where such graphics are available, but we are looking for something with a bit more imagination and flexibility.
This graphic should be targeted to web sites and be delivered with vector-based (SVG) graphics.

```html
<!DOCTYPE html>
<html lang="en">
<head>
<meta charset="utf-8">
<title>Four in One – Super Product</title>
<link href="https://fonts.googleapis.com/css2?family=Barlow:wght@500&family=Barlow+Semi+Condensed:wght@800&family=Poppins:wght@400;800&display=swap" rel="stylesheet">
<style>
  :root{
    --green:#3cc98a; --green-dark:#0a9a4a;
    --violet:#c65cf0; --purple:#8b4fb8; --navy:#1f4e9a;
    --blue:#0b6fbf; --cyan:#14c8e6; --teal:#10a8d8;
    --core:#0433a5; --ink:#2a2a2a; --body:#333;
  }
  html,body{margin:0;padding:0;width:1200px;height:927px;overflow:hidden;background:#fff;}
  .infographic{display:block;width:1200px;height:927px;}
  .heading{font-family:"Barlow Semi Condensed",sans-serif;font-weight:800;font-size:27px;letter-spacing:.5px;}
  .heading--docs{fill:var(--green);}
  .heading--security{fill:var(--purple);}
  .heading--erp{fill:var(--blue);}
  .heading--digital{fill:var(--teal);}
  .summary{font-family:"Poppins",sans-serif;font-size:10.2px;fill:var(--body);}
  .feature{font-family:"Barlow",sans-serif;font-weight:500;font-size:14px;fill:var(--ink);letter-spacing:.3px;}
  .core-title{font-family:"Poppins",sans-serif;font-weight:800;fill:#fff;}
  .end{text-anchor:end;}
  .icon{fill:none;stroke-width:2.4;stroke-linecap:round;stroke-linejoin:round;}
</style>
</head>
<body>
<svg class="infographic" viewBox="0 0 1200 927" width="1200" height="927" xmlns="http://www.w3.org/2000/svg">
  <defs>
    <linearGradient id="ringStroke" x1="0" y1="0" x2="1" y2="0">
      <stop offset="0" stop-color="#3cc98a"/>
      <stop offset=".45" stop-color="#9b2f94"/>
      <stop offset=".65" stop-color="#8aa7d8"/>
      <stop offset="1" stop-color="#2e3a96"/>
    </linearGradient>
    <linearGradient id="docsStroke" x1="0" y1="1" x2="1" y2="0">
      <stop offset="0" stop-color="var(--green)"/><stop offset="1" stop-color="var(--green-dark)"/>
    </linearGradient>
    <linearGradient id="securityStroke" x1="0" y1="0" x2="1" y2="1">
      <stop offset="0" stop-color="var(--violet)"/><stop offset=".6" stop-color="#6a4fc0"/><stop offset="1" stop-color="var(--navy)"/>
    </linearGradient>
    <linearGradient id="erpStroke" x1="0" y1="0" x2="1" y2="1">
      <stop offset="0" stop-color="#1667b8"/><stop offset="1" stop-color="#0b76c6"/>
    </linearGradient>
    <linearGradient id="digitalStroke" x1="0" y1="0" x2="1" y2="1">
      <stop offset="0" stop-color="#1a6fc0"/><stop offset=".5" stop-color="var(--cyan)"/><stop offset="1" stop-color="#1a6fc0"/>
    </linearGradient>
    <radialGradient id="cardFill" cx=".5" cy=".45" r=".65">
      <stop offset=".55" stop-color="#ffffff"/><stop offset="1" stop-color="#ececec"/>
    </radialGradient>
    <radialGradient id="coreFill" cx=".5" cy=".4" r=".6">
      <stop offset="0" stop-color="#0a3fb8"/><stop offset="1" stop-color="var(--core)"/>
    </radialGradient>
    <linearGradient id="beamV" x1="0" y1="0" x2="0" y2="1">
      <stop offset="0" stop-color="#0a3fb8" stop-opacity="0"/>
      <stop offset=".3" stop-color="#2ea7dc"/>
      <stop offset=".45" stop-color="#0a3fb8"/>
      <stop offset=".55" stop-color="#0a3fb8"/>
      <stop offset=".7" stop-color="#2ea7dc"/>
      <stop offset="1" stop-color="#0a3fb8" stop-opacity="0"/>
    </linearGradient>
    <linearGradient id="beamH" x1="0" y1="0" x2="1" y2="0">
      <stop offset="0" stop-color="#0a3fb8" stop-opacity="0"/>
      <stop offset=".25" stop-color="#2ea7dc"/>
      <stop offset=".42" stop-color="#0a3fb8"/>
      <stop offset=".58" stop-color="#0a3fb8"/>
      <stop offset=".75" stop-color="#2ea7dc"/>
      <stop offset="1" stop-color="#0a3fb8" stop-opacity="0"/>
    </linearGradient>
    <linearGradient id="rule" x1="0" y1="0" x2="1" y2="0">
      <stop offset="0" stop-color="#cfd6dc" stop-opacity="0"/>
      <stop offset=".4" stop-color="#cfd6dc"/>
      <stop offset="1" stop-color="#cfd6dc" stop-opacity="0"/>
    </linearGradient>
    <symbol id="tick" viewBox="0 0 24 24">
      <path d="M21 11.1V12a9 9 0 1 1-5.3-8.2" fill="none" stroke="currentColor" stroke-width="2" stroke-linecap="round"/>
      <path d="M21 5 11.5 14.5 8.5 11.5" fill="none" stroke="currentColor" stroke-width="2" stroke-linecap="round" stroke-linejoin="round"/>
    </symbol>
  </defs>

  <!-- outer ring -->
  <circle class="ring" cx="602" cy="463" r="385" fill="none" stroke="url(#ringStroke)" stroke-width="4"/>

  <!-- connecting beams -->
  <rect class="beam" x="592" y="146" width="20" height="633" fill="url(#beamV)"/>
  <rect class="beam" x="287" y="454" width="633" height="20" fill="url(#beamH)"/>

  <!-- cards -->
  <path class="card card--docs" d="M297,101 H523 A59,59 0 0 1 582,160 V333 A131,131 0 0 0 472,444 H297 A59,59 0 0 1 238,385 V160 A59,59 0 0 1 297,101 Z" fill="url(#cardFill)" stroke="url(#docsStroke)" stroke-width="4"/>
  <path class="card card--security" d="M680,101 H905 A59,59 0 0 1 964,160 V385 A59,59 0 0 1 905,444 H732 A131,131 0 0 0 621,333 V160 A59,59 0 0 1 680,101 Z" fill="url(#cardFill)" stroke="url(#securityStroke)" stroke-width="4"/>
  <path class="card card--erp" d="M297,484 H472 A131,131 0 0 0 582,593 V768 A59,59 0 0 1 523,827 H297 A59,59 0 0 1 238,768 V543 A59,59 0 0 1 297,484 Z" fill="url(#cardFill)" stroke="url(#erpStroke)" stroke-width="4"/>
  <path class="card card--digital" d="M621,593 A131,131 0 0 0 732,484 H905 A59,59 0 0 1 964,543 V768 A59,59 0 0 1 905,827 H680 A59,59 0 0 1 621,768 Z" fill="url(#cardFill)" stroke="url(#digitalStroke)" stroke-width="4"/>

  <!-- core -->
  <circle class="core" cx="602" cy="463" r="123" fill="url(#coreFill)"/>
  <text class="core-title" x="601" y="466" text-anchor="middle" font-size="52">SUPER</text>
  <text class="core-title" x="605" y="506" text-anchor="middle" font-size="44">PRODUCT</text>

  <!-- document management -->
  <g class="panel panel--docs">
    <text class="heading heading--docs" x="264" y="183">DOCUMENT</text>
    <text class="heading heading--docs" x="264" y="212">MANAGEMENT</text>
    <g class="icon" stroke="url(#docsStroke)">
      <path d="M478,150 H458 A9,9 0 0 0 449,159 V183 A6,6 0 0 0 455,189 H462 A7,7 0 0 1 469,196 V201 A8,8 0 0 0 477,209 H492 A8,8 0 0 0 500,201 V190"/>
      <circle cx="494" cy="164" r="15"/>
      <path d="M487,164 492,169 501,159"/>
    </g>
    <text class="summary" x="264" y="241">
      <tspan x="264">Streamline document organization, access, and</tspan>
      <tspan x="264" dy="13">collaboration with easier file storage and sharing,</tspan>
      <tspan x="264" dy="13">leading to more effecient workflows.</tspan>
    </text>
    <g color="#3cc98a">
      <use href="#tick" x="264" y="296" width="14" height="14"/>
      <use href="#tick" x="264" y="323" width="14" height="14"/>
      <use href="#tick" x="264" y="349" width="14" height="14"/>
      <use href="#tick" x="264" y="377" width="14" height="14"/>
    </g>
    <text class="feature" x="289" y="307">Centralized Document Control</text>
    <text class="feature" x="289" y="336" font-size="13.2">Collaborative Workspace Integration</text>
    <text class="feature" x="289" y="361">Automated Compliance Tracking</text>
    <text class="feature" x="289" y="389">Check 4</text>
    <rect x="281" y="316" width="165" height="1" fill="url(#rule)"/>
    <rect x="281" y="344" width="165" height="1" fill="url(#rule)"/>
    <rect x="281" y="370" width="165" height="1" fill="url(#rule)"/>
  </g>

  <!-- security & compliance -->
  <g class="panel panel--security">
    <text class="heading heading--security end" x="943" y="183">SECURITY &amp;</text>
    <text class="heading heading--security end" x="943" y="212">COMPLIANCE</text>
    <g class="icon" stroke="url(#securityStroke)">
      <path d="M742,194 A14,14 0 0 1 740,167 A17,17 0 0 1 772,162 A13,13 0 0 1 780,190"/>
      <path d="M757,182 768,178 779,182 V194 C779,202 773,207 768,209 C763,207 757,202 757,194 Z"/>
      <path d="M763,193 767,197 774,189"/>
    </g>
    <text class="summary end" x="943" y="241">
      <tspan x="943">Benefit from tailored cloud solutions, secure</tspan>
      <tspan x="943" dy="13">data storage, and expert disaster recovery</tspan>
      <tspan x="943" dy="13">planning for reliable and scalable IT operations.</tspan>
    </text>
    <g color="#7b3fb0">
      <use href="#tick" x="928" y="292" width="14" height="14"/>
      <use href="#tick" x="928" y="319" width="14" height="14"/>
      <use href="#tick" x="928" y="346" width="14" height="14"/>
      <use href="#tick" x="928" y="372" width="14" height="14"/>
    </g>
    <text class="feature end" x="919" y="304">Custom cloud Solutions</text>
    <text class="feature end" x="919" y="331">Secure Data Storage</text>
    <text class="feature end" x="919" y="358">Expert Disaster Recovery</text>
    <text class="feature end" x="919" y="385">Check 4</text>
    <rect x="760" y="313" width="165" height="1" fill="url(#rule)"/>
    <rect x="760" y="340" width="165" height="1" fill="url(#rule)"/>
    <rect x="760" y="367" width="165" height="1" fill="url(#rule)"/>
  </g>

  <!-- enterprise resource planning -->
  <g class="panel panel--erp">
    <text class="heading heading--erp" x="264" y="554">ENTERPRISE</text>
    <text class="heading heading--erp" x="264" y="583">RESOURCE</text>
    <text class="heading heading--erp" x="264" y="612">PLANNING</text>
    <g class="icon" stroke="var(--blue)">
      <path d="M434,588 A32,32 0 0 1 470,538"/>
      <path d="M464,531 470,538 463,544"/>
      <path d="M466,582 A32,32 0 0 1 430,595"/>
      <path d="M436,601 430,595 437,590"/>
      <path d="M450,553 l2,-5 h6 l2,5 l5,2 l5,-2 l4,4 l-2,5 l2,5 l5,2 v6 l-5,2 l-2,5 l2,5 l-4,4 l-5,-2 l-5,2 l-2,5 h-6 l-2,-5 l-5,-2 l-5,2 l-4,-4 l2,-5 l-2,-5 l-5,-2 v-6 l5,-2 l2,-5 l-2,-5 l4,-4 l5,2 Z" transform="translate(-6,6) scale(1)" />
      <circle cx="449" cy="567" r="5.5"/>
    </g>
    <text class="summary" x="264" y="639">
      <tspan x="264">Simplify management across finance, sales, and</tspan>
      <tspan x="264" dy="13">operations, enabling better decision-making and</tspan>
      <tspan x="264" dy="13">improved productivity.</tspan>
    </text>
    <g color="#0b6fbf">
      <use href="#tick" x="264" y="694" width="14" height="14"/>
      <use href="#tick" x="264" y="721" width="14" height="14"/>
      <use href="#tick" x="264" y="748" width="14" height="14"/>
      <use href="#tick" x="264" y="776" width="14" height="14"/>
    </g>
    <text class="feature" x="294" y="706">Integrated Business Processes</text>
    <text class="feature" x="294" y="733">Enhanced Decision-Making</text>
    <text class="feature" x="294" y="760">Productivity Improvement</text>
    <text class="feature" x="294" y="788">Check 4</text>
    <rect x="281" y="715" width="165" height="1" fill="url(#rule)"/>
    <rect x="281" y="742" width="165" height="1" fill="url(#rule)"/>
    <rect x="281" y="769" width="165" height="1" fill="url(#rule)"/>
  </g>

  <!-- digital transformation -->
  <g class="panel panel--digital">
    <g class="icon" stroke="url(#digitalStroke)">
      <path d="M792,555 V535 A7,7 0 0 0 785,528 H767 A7,7 0 0 0 760,535 V568 A7,7 0 0 0 767,575 H787"/>
      <path d="M760,538 H792"/>
      <path d="M768,552 h3 M775,552 h8 M768,561 h3 M775,561 h4"/>
      <circle cx="796" cy="565" r="8"/>
      <path d="M802,571 808,577"/>
    </g>
    <text class="heading heading--digital end" x="943" y="586">DIGITAL</text>
    <text class="heading heading--digital end" x="943" y="615">TRANSFORMATION</text>
    <text class="summary end" x="943" y="639">
      <tspan x="943">Turn scanned documents into easily</tspan>
      <tspan x="943" dy="13">searchable digital archives, boosting</tspan>
      <tspan x="943" dy="13">effeciency and accessibility.</tspan>
    </text>
    <g color="#14b8e0">
      <use href="#tick" x="929" y="695" width="14" height="14"/>
      <use href="#tick" x="929" y="722" width="14" height="14"/>
      <use href="#tick" x="929" y="750" width="14" height="14"/>
      <use href="#tick" x="929" y="777" width="14" height="14"/>
    </g>
    <text class="feature end" x="921" y="707">Instant searchable Archives with OCR</text>
    <text class="feature end" x="921" y="734">Automated Document Classification</text>
    <text class="feature end" x="921" y="761">TeamVault and Cloud Blob Ready</text>
    <text class="feature end" x="921" y="789">Check 4</text>
    <rect x="760" y="716" width="165" height="1" fill="url(#rule)"/>
    <rect x="760" y="743" width="165" height="1" fill="url(#rule)"/>
    <rect x="760" y="770" width="165" height="1" fill="url(#rule)"/>
  </g>
</svg>
</body>
</html>
```